Covid 19 Exit Strategy one page brochure

I would like to design, and will need URGENT help, a brochure detailing a Covid 19 Exit Strategy plan. This brochure will need to be understood easily and the graphics inside should make it easy for people to understand without reading the entire text. This project is quite urgent and needs to be completed THIS WEEK - by Saturday may 16th at the latest. I am attaching two examples. I will provide the text.

```html
<!DOCTYPE html>
<html lang="en">
<head>
<meta charset="utf-8">
<title>COVID-19 Phased Exit Strategy</title>
<link href="https://fonts.googleapis.com/css2?family=Poppins:wght@400;500;600;700;800&family=Montserrat:wght@400;500;600&display=swap" rel="stylesheet">
<style>
:root{
  --navy:#1b2f57;
  --navy-dark:#0f1f3f;
  --red:#e42226;
  --blue:#3aa3dd;
  --white:#ffffff;
  --ink:#2b2b2b;
  --page:#dcdcdc;
  --icon-red:#f4c5c6;
  --icon-blue:#c7e3f4;
}
*{box-sizing:border-box;margin:0;padding:0}
html,body{width:1200px;height:4000px;overflow:hidden;background:var(--page)}
body{font-family:"Montserrat",Arial,sans-serif;color:var(--ink)}
.brochure{position:absolute;left:216px;top:155px;width:768px;height:3687px;display:flex;flex-direction:column;overflow:hidden}

.masthead{flex:0 0 207px;background:linear-gradient(180deg,#24386a,var(--navy-dark));text-align:center;padding-top:30px;font-family:"Poppins",sans-serif}
.masthead h1{color:var(--white);font-size:42px;font-weight:800;line-height:1.1}
.masthead .headline{color:var(--red);font-size:44px;font-weight:800;line-height:1.12}
.masthead .byline{color:var(--white);font-size:31px;font-weight:500;line-height:1.25}

.requirements{flex:0 0 410px;background:var(--red);color:var(--white);padding:14px 38px 0}
.requirements .intro{font-size:9.4px;line-height:1.42;text-align:justify;font-weight:500}
.pill{display:block;width:max-content;margin:12px auto 12px;background:var(--white);font-family:"Poppins",sans-serif;font-weight:700;padding:2px 30px;clip-path:polygon(7% 0,100% 0,93% 100%,0 100%)}
.requirements .pill{color:var(--red);font-size:22px}
.req-list{display:flex;gap:50px}
.req-col{flex:1;display:flex;flex-direction:column;gap:13px}
.req{display:flex;gap:9px;align-items:center;font-size:10.4px;line-height:1.38;font-weight:500}
.req p{text-align:justify}
.req .num{flex:0 0 21px;height:21px;border-radius:50%;background:var(--white);color:var(--red);font-family:"Poppins",sans-serif;font-weight:700;font-size:13px;display:flex;align-items:center;justify-content:center}

.plan-band{flex:0 0 59px;background:var(--navy-dark);color:var(--white);font-family:"Poppins",sans-serif;font-weight:700;font-size:25px;display:flex;align-items:center;justify-content:center}

.stage{padding:0 38px;color:var(--white);overflow:hidden;display:flex;flex-direction:column}
.stage.blue{background:var(--blue)}
.stage.red{background:var(--red)}
.stage-1{flex:0 0 1037px}
.stage-2{flex:0 0 1044px}
.stage-3{flex:0 0 871px}
.stage .pill{font-size:30px;line-height:1.3;margin:3px auto 10px;padding:0 32px}
.stage.blue .pill{color:var(--blue)}
.stage.red .pill{color:var(--red)}
.stage .entry{font-size:13.6px;line-height:1.32;text-align:center;font-weight:500;padding:0 10px}
.stage .sequence{font-size:13.6px;text-align:center;margin:8px 0 12px}
.measures{background:var(--white);outline:3px solid rgba(255,255,255,.7);outline-offset:2px;padding:18px 22px 18px;color:var(--ink);display:flex;flex-direction:column}
.stage-1 .measures{height:872px}
.stage-2 .measures{height:845px}
.stage-3 .measures{height:660px}
.measure-cols{flex:1;display:flex;gap:38px}
.measure-col{flex:1;display:flex;flex-direction:column;justify-content:space-between}
.measure{display:flex;gap:30px;align-items:center;font-size:9.9px;line-height:1.45}
.measure p{text-align:justify;flex:1}
.icon{flex:0 0 62px;height:62px;border-radius:8px;background:var(--icon-blue)}
.stage.red .icon{background:var(--icon-red)}
.measure.wide{margin-top:16px;gap:22px}

.footer{flex:0 0 59px;display:flex;background:var(--red)}
.footer .issuer{width:210px;background:var(--white);display:flex;align-items:center;gap:10px;padding:0 14px;margin:5px 0 5px 39px;font-size:10px;font-weight:600;color:var(--red)}
.footer .issuer .mark{width:20px;height:20px;background:var(--red)}
.footer .tag,.footer .contact{color:var(--white);padding:14px 0 0 18px;font-size:11px;line-height:1.4}
.footer .tag{width:275px}
.footer strong{font-family:"Poppins",sans-serif;font-weight:600}
</style>
</head>
<body>
<div class="brochure">

  <header class="masthead">
    <h1>COVID-19</h1>
    <div class="headline">PHASED EXIT STRATEGY</div>
    <div class="byline">Developed by Lena Dorvalis</div>
  </header>

  <section class="requirements">
    <p class="intro">Pandemics have, historically, seen their end both medically - via herd immunity or immunizations. And while there are several clinical trials underway for potential Covid-19 vaccines, we are still a long way from deploying an effective vaccine and one that will stand the test of time as the virus changes. Covid-19 pandemic will be considered 'ended' when there are only occasional traces of localized cases that are quickly contained in specific locations. Today and in the absence of an effective vaccine(s) and for the re-opening of the economies and social activities to be successful, it is critical that the following basic conditions be in place before any lockdowns are lifted and before social activities resume:</p>
    <span class="pill">GENERAL REQUIREMENTS</span>
    <div class="req-list">
      <div class="req-col">
        <div class="req"><span class="num">1</span><p>Single digit downward trend of documented cases within the past 14- days.</p></div>
        <div class="req"><span class="num">2</span><p>Hospitals and the health care system are capable of treating patients without operating on a crisis mode.</p></div>
        <div class="req"><span class="num">3</span><p>Ability to screen and test symptomatic individuals within 24 hours of identification. Increased and sufficient testing capacity, to test at least 50% of all population if necessary within a timeframe of 3 months.</p></div>
        <div class="req"><span class="num">4</span><p>Ability to surge ICU capacity on a short notice - 24h.</p></div>
        <div class="req"><span class="num">5</span><p>Ability to track and trace infected patients and contacts on a live basis and across the country and ability to react quickly to any unusual trends or outbreaks.</p></div>
      </div>
      <div class="req-col">
        <div class="req"><span class="num">6</span><p>Plan in place to trigger targeted or full-scale containment in case of sudden outbreaks</p></div>
        <div class="req"><span class="num">7</span><p>Mandatory use of masks (at least surgical grade) for everyone in all public areas and at work. Mandatory use of N95, or equivalent, masks for all healthcare front workers and for all government agencies and authorities that are involved in overseeing the containment activities.</p></div>
        <div class="req"><span class="num">8</span><p>Mandatory daily checks of body temperature for everyone at the workplace or entering public areas.</p></div>
        <div class="req"><span class="num">9</span><p>Mandatory sanitation in all places - use of disinfection available on a large scale.</p></div>
      </div>
    </div>
  </section>

  <div class="plan-band">PHASED COVID-19 LOCKDOWN EXIT STRATEGY PLAN</div>

  <section class="stage blue stage-1">
    <span class="pill">STAGE : 1</span>
    <p class="entry">To enter this stage, additional to the general requirements, the Effective Reproduction Number (Rt) must be less than 1 and the death rate at less than 3%.</p>
    <p class="sequence">The economy and social activities can resume in this sequence:</p>
    <div class="measures">
      <div class="measure-cols">
        <div class="measure-col">
          <div class="measure"><div class="icon" role="img" aria-label="Elderly person icon"></div><p>Elderly (60+ years old) and vulnerable individuals should continue to self-isolate.</p></div>
          <div class="measure"><div class="icon" role="img" aria-label="Work from home icon"></div><p>Work from home should continue whenever and as much as possible.</p></div>
          <div class="measure"><div class="icon" role="img" aria-label="No travel icon"></div><p>Non-essential travel should be minimized between cities and regions (and within cities and regions where covid-19 infections are still a risk)</p></div>
          <div class="measure"><div class="icon" role="img" aria-label="Factory icon"></div><p>Large businesses (300 people and more, manufacturing, services, etc.) can reopen progressively. Common areas should remain closed (cafeteria, restaurant, gym, meeting rooms of no more than 5 people).</p></div>
          <div class="measure"><div class="icon" role="img" aria-label="Coffee shop icon"></div><p>Coffee &amp; restaurants can reopen but must operate at 30% capacity as well and comply with social distancing. Clients must wear as much as possible their masks if they are not consuming food/coffee. Clients should avoid to talking to each other with masks off.</p></div>
          <div class="measure"><div class="icon" role="img" aria-label="Closed stadium icon"></div><p>Large scale events (cinema, theaters, sport, business conferences, etc.) should remain closed or operate virtually. Sport events can resume but without spectators. Athletes and the staff surrounding them should be tested, disinfectants should be available and masks used as much as reasonably possible.</p></div>
          <div class="measure"><div class="icon" role="img" aria-label="Closed school icon"></div><p>All schools should remain closed. On-line courses should continue to be the preferred method for education.</p></div>
        </div>
        <div class="measure-col">
          <div class="measure"><div class="icon" role="img" aria-label="No gathering icon"></div><p>No more than 5 people maximum gathering at a time in public areas and at work.</p></div>
          <div class="measure"><div class="icon" role="img" aria-label="Social distancing icon"></div><p>Social distancing should continue to be re-enforced in public areas, at work and in all areas reopened.</p></div>
          <div class="measure"><div class="icon" role="img" aria-label="Small shop icon"></div><p>Small businesses (300 people and less) can reopen as well with the same conditions as large businesses.</p></div>
          <div class="measure"><div class="icon" role="img" aria-label="Hotel icon"></div><p>Hotels &amp; tourism (museums, etc.) can reopen but must operate at 30% or less capacity. All common areas (restaurants, gyms, swimming pools, conference rooms, etc.) should remain closed.</p></div>
          <div class="measure"><div class="icon" role="img" aria-label="Church icon"></div><p>Religious sites can reopen with a maximum capacity of 30% or less. Social distancing and wearing masks is mandatory. Religious sites should organize (volunteers can help) to check body temperature of everyone accessing the site and provide disinfectant at entry.</p></div>
          <div class="measure"><div class="icon" role="img" aria-label="Pharmacy icon"></div><p>Pharmacies will continue to be open. However, they must make available disinfectant for use by clients and will continue to comply with social distancing. Pharmacies should limit the number of client/patient in their stores not to exceed 30% of the standard capacity.</p></div>
          <div class="measure"><div class="icon" role="img" aria-label="Commercial shop icon"></div><p>Commercial shops can reopen. Shops should control the flow of people in their facilities not to exceed 30% at a time of standard capacity. Shops should provide disinfectant and temperature control at entry.</p></div>
        </div>
      </div>
      <div class="measure wide"><div class="icon" role="img" aria-label="Transport truck icon"></div><p>Transportation (buses, taxis, airlines) will resume progressively. No air travels permitted in and out of Covid-19 known hotspots, locally or internationally. Entry to country should be limited and strictly controlled. All landing passengers and visitors regardless of the country of origin should be tested for Covid-19 at arrival. All passengers and visitors will undergo a temperature check at arrival. No more than 3 people at a time in a taxi/ride-share including the driver. All passengers wearing masks. Buses could operate with no more than 30% customer's capacity per bus.</p></div>
    </div>
  </section>

  <section class="stage red stage-2">
    <span class="pill">STAGE : 2</span>
    <p class="entry">To enter stage 2 of the Covid-19 Exit Strategy, compliance to the general requirements is compulsory, additional to a successful Stage 1 outcome. The Effective Reproduction Number (Rt) for Stage 2 must be less than 0.5 and the death rate stabilized at less than 1.5%.</p>
    <p class="sequence">The economy and social activities can resume in this sequence:</p>
    <div class="measures">
      <div class="measure-cols">
        <div class="measure-col">
          <div class="measure"><div class="icon" role="img" aria-label="Elderly person icon"></div><p>Elderly (60+ years old) and vulnerable individuals should continue to self-isolate as much as possible.</p></div>
          <div class="measure"><div class="icon" role="img" aria-label="Work from home icon"></div><p>Work from home should if possible or for jobs that do not have to be necessarily in an office setup.</p></div>
          <div class="measure"><div class="icon" role="img" aria-label="Travel icon"></div><p>Travel can resume between cities and regions. The same containment restrictions should apply to any existing hotspot.</p></div>
          <div class="measure"><div class="icon" role="img" aria-label="Factory icon"></div><p>Large businesses (300 people and more, manufacturing, services, etc.) will continue to operate. Common areas should open but social distancing should remain (cafeteria, restaurant, gym, meeting rooms of no more than 10 people).</p></div>
          <div class="measure"><div class="icon" role="img" aria-label="Small shop icon"></div><p>Small businesses (300 people and less) will continue to operate with the same conditions as large businesses.</p></div>
          <div class="measure"><div class="icon" role="img" aria-label="Commercial shop icon"></div><p>Commercial shops will continue to be open and can operate at 50% capacity. Wear of masks should continue.</p></div>
          <div class="measure"><div class="icon" role="img" aria-label="Pharmacy icon"></div><p>Pharmacies will continue to be open and will need to operate a 50% capacity</p></div>
          <div class="measure"><div class="icon" role="img" aria-label="Coffee shop icon"></div><p>Coffee &amp; restaurants can operate at 50% capacity and continue comply with social distancing. Clients must wear masks as much as possible their masks if they are not consuming food/coffee.</p></div>
        </div>
        <div class="measure-col">
          <div class="measure"><div class="icon" role="img" aria-label="No gathering icon"></div><p>No more than 10 people maximum gathering at a time in public areas and at work.</p></div>
          <div class="measure"><div class="icon" role="img" aria-label="Social distancing icon"></div><p>Social distancing can be relaxed. However people should continue to wear masks and use disinfectants.</p></div>
          <div class="measure"><div class="icon" role="img" aria-label="Hospital icon"></div><p>Elective surgeries can resume in hospitals and clinics that are equipped to comply with all general requirements.</p></div>
          <div class="measure"><div class="icon" role="img" aria-label="Church icon"></div><p>Religious sites can operate with a maximum capacity of 50%. Social distancing and wearing masks should be enforced. Sites should continue to check body temperature of everyone accessing the site and provide disinfectant at entry.</p></div>
          <div class="measure"><div class="icon" role="img" aria-label="School icon"></div><p>Schools can reopen in parallel with on-line education. Social distancing and re-arranging school seating to prevent the spread of infection is mandatory.</p></div>
          <div class="measure"><div class="icon" role="img" aria-label="Stadium icon"></div><p>Large scale events (cinema, theaters, sport, business conferences, etc.) could resume under strict social distancing. People should wear masks.</p></div>
          <div class="measure"><div class="icon" role="img" aria-label="Hotel icon"></div><p>Hotels &amp; tourism (museums, etc.) can operate at 50% capacity. All common areas (restaurants, gyms, swimming pools, conference rooms, etc.) could reopen. Gatherings are limited to 10 people or less and can be expanded with social distancing and wearing protective masks.</p></div>
        </div>
      </div>
      <div class="measure wide"><div class="icon" role="img" aria-label="Transport truck icon"></div><p>Transportation (buses, taxis, and airlines) will continue to operate. Still no air travels permitted in and out of Covid-19 known hotspots, locally or internationally. Entry to country should be relaxed but remain controlled. Airports should continue to use thermo cameras to monitor passenger's temperature at landing. Airports should be equipped to test for Covid-19 if necessary. Transportation by taxi/ride-share continues, however, passengers wear masks. Buses could operate with 50% capacity per bus.</p></div>
    </div>
  </section>

  <section class="stage blue stage-3">
    <span class="pill">STAGE : 3</span>
    <p class="entry">To enter stage 3 of the Covid-19 Exit Strategy, compliance to the general requirements is compulsory, additional to a successful Stage 2 outcome. The Effective Reproduction Number (Rt) for Stage 3 must be less than 0.3 and the death rate stabilized at less than 1%.</p>
    <p class="sequence">The economy and social activities can resume in this sequence:</p>
    <div class="measures">
      <div class="measure-cols">
        <div class="measure-col">
          <div class="measure"><div class="icon" role="img" aria-label="Elderly person icon"></div><p>Elderly (60+ years old) and vulnerable individuals may resume all previously exercised activities without restrictions.</p></div>
          <div class="measure"><div class="icon" role="img" aria-label="Luggage icon"></div><p>Travel can resume between cities and regions and out of country travel. The same containment restrictions as Stage 1 and 2 would continue to apply to any existing hotspot.</p></div>
          <div class="measure"><div class="icon" role="img" aria-label="Factory icon"></div><p>Large businesses (300 people and more, manufacturing, services, etc.) will resume normal business practices. Wear of masks is recommended but not mandatory.</p></div>
          <div class="measure"><div class="icon" role="img" aria-label="Small shop icon"></div><p>Small businesses (300 people and less) will operate with the same conditions as large businesses.</p></div>
          <div class="measure"><div class="icon" role="img" aria-label="Coffee shop icon"></div><p>Coffee &amp; restaurants can resume normal operations. Clients may wear masks for personal protection if they wish to.</p></div>
          <div class="measure"><div class="icon" role="img" aria-label="Hotel icon"></div><p>Hotels &amp; tourism (museums, etc.) can operate at 100% capacity including all common areas</p></div>
        </div>
        <div class="measure-col">
          <div class="measure"><div class="icon" role="img" aria-label="Social distancing icon"></div><p>Restrictions as to the number of people gathering together can be lifted. Social distancing can be relaxed. However, wear of masks may continue.</p></div>
          <div class="measure"><div class="icon" role="img" aria-label="Hospital icon"></div><p>All hospital and clinic surgeries can resume in hospitals in compliance with standard hospital and health care procedures.</p></div>
          <div class="measure"><div class="icon" role="img" aria-label="Commercial shop icon"></div><p>Commercial shops can operate on a normal mode - previous to covid- 19. Wear of masks could be recommended in certain areas.</p></div>
          <div class="measure"><div class="icon" role="img" aria-label="Pharmacy icon"></div><p>Pharmacies can operate at a normal state.</p></div>
          <div class="measure"><div class="icon" role="img" aria-label="Stadium icon"></div><p>Large scale events (cinema, theaters, sport, business conferences, etc.) could resume under moderate social distancing. People may elect to wear masks.</p></div>
          <div class="measure"><div class="icon" role="img" aria-label="Church icon"></div><p>Religious sites can operate normally. Wear of masks should be elective.</p></div>
          <div class="measure"><div class="icon" role="img" aria-label="School icon"></div><p>Schools can resume operations. Re-arranging school seating should continue until a vaccine is found.</p></div>
        </div>
      </div>
      <div class="measure wide"><div class="icon" role="img" aria-label="Transport truck icon"></div><p>Transportation (buses, taxis, and airlines) will operate at a normal capacity. Still no air travels permitted in and out of Covid-19 known hotspots, locally or internationally. Entry to country should be relaxed and operate normally. Airports should continue to use thermo cameras to monitor passenger's temperature at landing. Airports should be equipped to test for Covid-19 if necessary. Transportation by taxi/ride-share and buses will resume on a normal mode. Wear of masks is elective.</p></div>
    </div>
  </section>

  <footer class="footer">
    <div class="issuer"><span class="mark"></span><span>Public Health Office</span></div>
    <div class="tag"><strong>#STAYHOMESAFE</strong><br>Don't have to go outside? Please stay at home!</div>
    <div class="contact"><strong>FOR INFORMATION</strong><br>
      <svg width="10" height="10" viewBox="0 0 24 24" fill="#fff" aria-hidden="true"><path d="M6.6 10.8a15 15 0 006.6 6.6l2.2-2.2a1 1 0 011-.25 11.4 11.4 0 003.6.57 1 1 0 011 1V20a1 1 0 01-1 1A17 17 0 013 4a1 1 0 011-1h3.5a1 1 0 011 1c0 1.25.2 2.45.57 3.6a1 1 0 01-.25 1z"/></svg>
      8000 - 1234 &nbsp; www.healthinfo-example.org</div>
  </footer>

</div>
</body>
</html>
```